Anzeigengestaltung für Verkauf & Installation von Alarmanlagen und Videoüberwachungssystemen
Zielgruppe
Verkauf und Installation von Alarmanlagen und Videoüberwachungssystemen.
Verkauf erfolgt über eigenen Onlineshop.
Installation der Anlagen im regionalen Umkreis, hauptsächlich Privatkunden.
Zielgruppe: Privatkunden, Familien, mit vorhandener Immobilie/Wohneigentum.
Aufgabenstellung
Zeitungsformat:
92 mm x 60 mm
s/w-4C
Text Entwurf als Orientierung befindet sich im Anhang, ebenso das Firmenlogo.
Bilder aus der Webseite sind ebenfalls beigefügt. Vielleicht lässt sich damit etwas anfangen, ich bin aber auch für Vorschläge aus geeigneten Stock-Bildern offen.

```html
<!DOCTYPE html>
<html lang="de">
<head>
<meta charset="utf-8">
<title>Funkschutz Lindenhof – Anzeige</title>
<link rel="stylesheet" href="https://fonts.googleapis.com/css2?family=Roboto+Condensed:wght@400;700&display=swap">
<style>
  :root {
    --red: #d8402f;
    --ink: #2b2b2b;
    --paper-light: #f4f4f4;
    --paper-dark: #dedede;
    --stage: #ececec;
    --photo-blue: #1f3f8f;
    --photo-wood: #a9582a;
    --photo-dark: #1d2233;
  }
  * { margin: 0; padding: 0; box-sizing: border-box; }
  html, body { width: 1200px; height: 2400px; overflow: hidden; }
  body {
    background: var(--stage);
    font-family: "Roboto Condensed", "Arial Narrow", sans-serif;
    color: var(--ink);
    position: relative;
  }
  .ad {
    position: absolute;
    left: 50px; top: 841px;
    width: 1100px; height: 717px;
    overflow: hidden;
    background: linear-gradient(135deg, var(--paper-light) 0%, #ffffff 45%, var(--paper-dark) 100%);
  }
  .ad * { white-space: nowrap; }
  .ad-photo { position: absolute; left: 0; top: 0; width: 1100px; height: 717px; }
  .brand {
    position: absolute; left: 560px; top: 70px;
    display: flex; align-items: center; gap: 18px;
  }
  .brand-dot { width: 96px; height: 96px; border-radius: 50%; background: var(--ink); flex: none; }
  .brand-name { font-size: 38px; font-weight: 700; line-height: 1; color: var(--ink); }
  .brand-tagline { font-size: 15px; font-weight: 400; margin-top: 8px; color: var(--ink); }
  .headline {
    position: absolute; left: 600px; top: 232px;
    font-size: 34px; font-weight: 700; line-height: 1; letter-spacing: 0.3px;
  }
  .benefits { position: absolute; left: 600px; top: 295px; list-style: none; }
  .benefits li {
    display: flex; align-items: center; gap: 12px;
    font-size: 28px; font-weight: 700; color: var(--red);
    height: 42px;
  }
  .benefits svg { width: 28px; height: 28px; flex: none; }
  .funding-band {
    position: absolute; left: 583px; top: 457px;
    width: 517px; height: 68px;
    background: var(--red);
    border-radius: 34px 0 0 34px;
    color: #fff; font-size: 31px; font-weight: 700;
    display: flex; align-items: center; padding-left: 46px;
  }
  .services {
    position: absolute; left: 600px; top: 555px;
    display: flex; gap: 24px; align-items: center;
  }
  .service { display: flex; align-items: center; gap: 8px; font-size: 21px; font-weight: 700; }
  .service svg { height: 36px; flex: none; }
  .contact {
    position: absolute; right: 28px; top: 622px;
    text-align: right; font-size: 20px; font-weight: 700; line-height: 32px;
  }
  .contact .sep { color: var(--red); }
</style>
</head>
<body>
  <section class="ad" aria-label="Anzeige Funkschutz Lindenhof">
    <svg class="ad-photo" viewBox="0 0 1100 717">
      <defs>
        <linearGradient id="photoTone" x1="0" y1="0" x2="1" y2="0.3">
          <stop offset="0" stop-color="#a9582a"/>
          <stop offset="0.35" stop-color="#6b3a22"/>
          <stop offset="0.6" stop-color="#1f3f8f"/>
          <stop offset="1" stop-color="#1d2233"/>
        </linearGradient>
      </defs>
      <polygon role="img" aria-label="Foto: vermummter Einbrecher hebelt ein Holzfenster an einer Backsteinwand auf"
               points="0,0 422,0 530,330 373,717 0,717" fill="url(#photoTone)"/>
      <polyline points="422,0 530,330 373,717" fill="none" stroke="#d8402f" stroke-width="5"/>
    </svg>

    <div class="brand">
      <div class="brand-dot"></div>
      <div>
        <div class="brand-name">Funkschutz Lindenhof</div>
        <div class="brand-tagline">Schützen Sie sich und Ihr Eigentum</div>
      </div>
    </div>

    <h1 class="headline">MODERNE FUNKALARMANLAGEN</h1>

    <ul class="benefits">
      <li><svg viewBox="0 0 30 30"><rect x="2" y="6" width="20" height="20" fill="none" stroke="#d8402f" stroke-width="3"/><path d="M7 15 L12 21 L28 3" fill="none" stroke="#d8402f" stroke-width="4"/></svg>Individuelle Beratung</li>
      <li><svg viewBox="0 0 30 30"><rect x="2" y="6" width="20" height="20" fill="none" stroke="#d8402f" stroke-width="3"/><path d="M7 15 L12 21 L28 3" fill="none" stroke="#d8402f" stroke-width="4"/></svg>Onlineshop</li>
      <li><svg viewBox="0 0 30 30"><rect x="2" y="6" width="20" height="20" fill="none" stroke="#d8402f" stroke-width="3"/><path d="M7 15 L12 21 L28 3" fill="none" stroke="#d8402f" stroke-width="4"/></svg>Installation</li>
    </ul>

    <div class="funding-band">STAATLICHE FÖRDERUNG MÖGLICH</div>

    <div class="services">
      <div class="service">
        <svg viewBox="0 0 60 40" width="54"><path d="M6 8 Q0 20 6 32 M54 8 Q60 20 54 32" fill="none" stroke="#2b2b2b" stroke-width="3"/><rect x="14" y="4" width="32" height="32" rx="6" fill="#d8402f"/><g fill="#fff"><rect x="19" y="10" width="22" height="5"/><rect x="19" y="19" width="5" height="4"/><rect x="27" y="19" width="5" height="4"/><rect x="35" y="19" width="5" height="4"/><rect x="19" y="26" width="5" height="4"/><rect x="27" y="26" width="5" height="4"/><rect x="35" y="26" width="5" height="4"/></g></svg>
        Alarm
      </div>
      <div class="service">
        <svg viewBox="0 0 40 40" width="36"><path d="M4 12 V4 H12 M28 4 H36 V12 M36 28 V36 H28 M12 36 H4 V28" fill="none" stroke="#2b2b2b" stroke-width="3"/><circle cx="20" cy="20" r="8" fill="none" stroke="#2b2b2b" stroke-width="3"/><circle cx="20" cy="20" r="4" fill="#d8402f"/></svg>
        Video
      </div>
      <div class="service">
        <svg viewBox="0 0 56 40" width="50"><path d="M4 20 L18 8 L32 20 V36 H4 Z" fill="none" stroke="#2b2b2b" stroke-width="3"/><rect x="14" y="24" width="8" height="12" fill="#d8402f"/><rect x="34" y="4" width="18" height="32" rx="3" fill="#2b2b2b"/><path d="M43 10 L49 22 H37 Z" fill="#d8402f"/></svg>
        Hausautomation
      </div>
    </div>

    <div class="contact">
      <div>Mühlgasse 12 <span class="sep">•</span> 71234 Wiesental <span class="sep">•</span> 07123-4567</div>
      <div>www.funkschutz-lindenhof.de&nbsp; E-Mail: info@funkschutz-lindenhof.de</div>
    </div>
  </section>
</body>
</html>
```